Asphalt Driveway Billboard Design

We need a billboard designed for an Asphalt & Concrete Company in Minnesota. We want to advertise Asphalt Driveways on this billboard! Logo is uploaded below. Our website is pinecrest-paving.com for more information.

```html
<!DOCTYPE html>
<html lang="en">
<head>
<meta charset="utf-8">
<title>Asphalt Driveways Billboard – Pinecrest Paving</title>
<link rel="stylesheet" href="https://fonts.googleapis.com/css2?family=Michroma&family=Poppins:wght@800&display=swap">
<style>
  :root {
    --page: #ffffff;
    --charcoal: #2a2828;
    --panel-light: #ffffff;
    --ink: #231f20;
    --blue: #1a7fc4;
    --blue-light: #35a8e6;
    --blue-deep: #0a5fa3;
    --photo-green: #6f8a55;
    --photo-tan: #c9bfae;
  }
  html, body {
    margin: 0;
    width: 1141px;
    height: 1200px;
    overflow: hidden;
    background: var(--page);
  }
  .billboard {
    position: absolute;
    left: 50px;
    top: 449px;
    width: 1041px;
    height: 303px;
    box-shadow: 0 6px 18px rgba(0,0,0,0.18);
  }
  .billboard svg { display: block; width: 100%; height: 100%; }
  .headline { font-family: "Michroma", sans-serif; }
  .phone { font-family: "Michroma", sans-serif; fill: var(--ink); }
  .website { font-family: "Poppins", sans-serif; font-weight: 800; fill: var(--ink); }
  .company-name { font-family: "Michroma", sans-serif; fill: var(--ink); }
</style>
</head>
<body>
<div class="billboard">
  <svg viewBox="0 0 1703 495" xmlns="http://www.w3.org/2000/svg">
    <defs>
      <linearGradient id="photoTones" x1="0" y1="0" x2="0" y2="1">
        <stop offset="0" stop-color="var(--photo-green)"/>
        <stop offset="0.45" stop-color="#8a6a55"/>
        <stop offset="0.6" stop-color="var(--photo-tan)"/>
        <stop offset="1" stop-color="#bdb6aa"/>
      </linearGradient>
      <linearGradient id="headlineBlue" x1="0" y1="0" x2="0" y2="1">
        <stop offset="0" stop-color="var(--blue-light)"/>
        <stop offset="1" stop-color="var(--blue-deep)"/>
      </linearGradient>
    </defs>

    <!-- panels -->
    <rect class="panel-light" x="0" y="0" width="1703" height="495" fill="var(--panel-light)"/>
    <rect class="panel-dark" x="540" y="0" width="1163" height="286" fill="var(--charcoal)"/>

    <!-- driveway photo area -->
    <rect x="0" y="0" width="460" height="495" fill="url(#photoTones)" role="img" aria-label="Photo of a house with a freshly paved driveway"/>

    <!-- curved accent bands -->
    <path class="curve-white" d="M330,0 H470 Q700,250 420,495 H330 Z" fill="var(--panel-light)"/>
    <path class="curve-black" d="M340,0 H420 Q610,250 380,495 H340 Q530,300 430,120 Q390,50 340,0 Z" fill="var(--charcoal)"/>
    <path class="curve-blue" d="M340,495 V380 Q420,320 445,160 Q490,340 380,495 Z" fill="var(--blue)"/>

    <!-- headline -->
    <text class="headline" x="610" y="165" font-size="128" textLength="1070" lengthAdjust="spacingAndGlyphs" fill="url(#headlineBlue)">ASPHALT</text>
    <text class="headline" x="615" y="272" font-size="112" textLength="1070" lengthAdjust="spacingAndGlyphs" fill="#ffffff">DRIVEWAYS</text>

    <!-- company name -->
    <circle cx="680" cy="350" r="34" fill="var(--blue)"/>
    <text class="company-name" x="680" y="432" font-size="34" text-anchor="middle" textLength="220" lengthAdjust="spacingAndGlyphs">PINECREST</text>
    <text class="company-name" x="680" y="466" font-size="20" text-anchor="middle" textLength="170" lengthAdjust="spacingAndGlyphs">PAVING</text>

    <!-- phone -->
    <circle cx="868" cy="366" r="27" fill="var(--blue)"/>
    <path d="M857,352 q-4,3 -1,10 q5,11 16,17 q7,3 10,-1 l2,-3 q1,-2 -1,-3 l-6,-4 q-2,-1 -3,1 l-2,2 q-6,-3 -9,-9 l2,-2 q2,-1 1,-3 l-4,-6 q-1,-2 -3,-1 z" fill="#ffffff"/>
    <text class="phone" x="918" y="393" font-size="62" textLength="707" lengthAdjust="spacingAndGlyphs">612-555-0148</text>

    <!-- website -->
    <text class="website" x="838" y="466" font-size="60" textLength="792" lengthAdjust="spacingAndGlyphs">www.Pinecrest-Paving.com</text>
  </svg>
</div>
</body>
</html>
```